Dalvick's Business Card

I need some designs for a new business card including the new logo attached. An old example of our business card is also attached to show all the data that should be included on the new design.
**I added some more examples someone had mocked up**

Contact Information for Business Card

Should include all info on other examples uploaded.

```html
<!DOCTYPE html>
<html lang="en">
<head>
<meta charset="utf-8">
<title>Dalvick's Business Card</title>
<link rel="stylesheet" href="https://fonts.googleapis.com/css2?family=Montserrat:wght@600;700;800&family=Questrial&display=swap">
<style>
  :root {
    --page: #e4e3e1;
    --card-top: #ffffff;
    --card-bottom: #ebebeb;
    --brand-blue: #0a67b1;
    --brand-red: #d9192a;
    --ink-light: #f4f4f4;
  }
  * { margin: 0; padding: 0; box-sizing: border-box; }
  html, body { width: 1200px; height: 1200px; overflow: hidden; background: var(--page); }
  .canvas { position: relative; width: 1200px; height: 1200px; }
  .card {
    position: absolute; left: 235px; width: 730px; height: 416px; overflow: hidden;
    background: linear-gradient(160deg, var(--card-top), var(--card-bottom));
  }
  .card--front { top: 160px; }
  .card--back { top: 632px; }
  .card__shapes { position: absolute; inset: 0; width: 100%; height: 100%; }
  .house-art {
    position: absolute; left: 18px; top: 125px; width: 265px; height: 143px;
    background: linear-gradient(180deg, var(--brand-red) 0%, var(--brand-blue) 70%);
  }
  .line { position: absolute; white-space: nowrap; transform: translateY(-50%); line-height: 1; }
  .service-area { left: 245px; top: 134px; font: 600 14px "Montserrat", sans-serif; color: var(--brand-red); }
  .brand-mark { position: absolute; border-radius: 50%; background: var(--brand-red); }
  .brand-name { font-family: "Montserrat", sans-serif; font-weight: 700; color: var(--brand-blue); }
  .front-name { left: 240px; top: 174px; font-size: 68px; }
  .front-mark { left: 130px; top: 140px; width: 74px; height: 74px; }
  .front-tagline { left: 245px; top: 218px; font: 700 17px "Montserrat", sans-serif; color: var(--brand-red); }
  .cta { left: 0; width: 730px; text-align: center; top: 384px; font: 16.5px "Questrial", sans-serif; color: var(--ink-light); letter-spacing: 0.4px; }
  .back-mark { left: 386px; top: 104px; width: 44px; height: 44px; }
  .back-name { left: 455px; top: 124px; font-size: 38px; }
  .back-tagline { left: 456px; top: 148px; font: 700 10px "Montserrat", sans-serif; color: var(--brand-red); }
  .family { left: 380px; top: 275px; font: 19.5px "Questrial", sans-serif; color: var(--ink-light); letter-spacing: 0.8px; }
  .person { left: 43px; top: 336px; font: 800 31px "Montserrat", sans-serif; color: var(--ink-light); }
  .licensed { left: 44px; top: 394px; font: 19.5px "Questrial", sans-serif; color: var(--ink-light); letter-spacing: 2px; }
  .contact { left: 380px; font: 21px "Questrial", sans-serif; color: var(--ink-light); display: flex; align-items: center; gap: 8px; }
  .contact--phone { top: 331px; }
  .contact--email { top: 362px; }
  .contact svg { width: 17px; height: 17px; fill: var(--ink-light); }
</style>
</head>
<body>
<main class="canvas">
  <section class="card card--front">
    <svg class="card__shapes" viewBox="0 0 1175 671" preserveAspectRatio="none" aria-hidden="true">
      <polygon fill="var(--brand-red)" points="0,565 550,565 588,528 625,565 1175,565 1175,671 0,671"/>
    </svg>
    <div class="line service-area">SERVES ELMRIDGE, IA &amp; SURROUNDING AREAS</div>
    <span class="brand-mark front-mark"></span>
    <div class="line brand-name front-name">DALVICK'S</div>
    <div class="line front-tagline">AIR CONDITIONING &amp; HEATING SERVICE</div>
    <div class="line cta">CALL TODAY FOR ALL YOUR HVAC, REFRIGERATION &amp; PLUMBING NEEDS</div>
  </section>

  <section class="card card--back">
    <svg class="card__shapes" viewBox="0 0 1175 671" preserveAspectRatio="none" aria-hidden="true">
      <polygon fill="var(--brand-red)" points="455,410 1175,410 1175,480 580,480"/>
      <polygon fill="var(--brand-blue)" points="0,430 491,430 580,480 1175,480 1175,635 580,635 515,598 0,598"/>
      <polygon fill="var(--brand-red)" points="0,598 515,598 580,635 1175,635 1175,671 0,671"/>
    </svg>
    <div class="house-art" role="img" aria-label="Illustration of a house with red roof, chimney and window"></div>
    <span class="brand-mark back-mark"></span>
    <div class="line brand-name back-name">DALVICK'S</div>
    <div class="line back-tagline">AIR CONDITIONING &amp; HEATING SERVICE</div>
    <div class="line family">FAMILY OWNED &amp; OPERATED</div>
    <div class="line person">MARK DALVICK</div>
    <div class="line licensed">LICENSED &amp; INSURED</div>
    <div class="line contact contact--phone">
      <svg viewBox="0 0 24 24" aria-hidden="true"><path d="M6.6 10.8a15 15 0 0 0 6.6 6.6l2.2-2.2c.3-.3.7-.4 1-.2 1.1.4 2.3.6 3.6.6.6 0 1 .4 1 1V20c0 .6-.4 1-1 1A17 17 0 0 1 3 4c0-.6.4-1 1-1h3.5c.6 0 1 .4 1 1 0 1.3.2 2.5.6 3.6.1.3 0 .7-.2 1z"/></svg>
      <span>555.014.2286</span>
    </div>
    <div class="line contact contact--email">
      <svg viewBox="0 0 24 24" aria-hidden="true"><path d="M2 5h20v2l-10 6L2 7z M2 9l10 6 10-6v10H2z"/></svg>
      <span>hvacdalvick@example.com</span>
    </div>
  </section>
</main>
</body>
</html>
```